BUSINESS CARD DESIGN

NAME- DALE VORSKIN
PHONE NUMER - 555- 714-9082
EMAIL- OFFICE@TRV-GROUNDMAKRZ.COM
BACK OF CARD- SPEACIALIZES IN LAND CLEARING, FORESTRY MUCLHING AND EXCAVATION

Contact Information for Business Card

NAME- DALE VORSKIN PHONE NUMER - 555- 714-9082 EMAIL- OFFICE@TRV-GROUNDMAKRZ.COM BACK OF CARD- SPEACIALIZES IN LAND CLEARING , MUCLHING AND EXCAVATION

```html
<!DOCTYPE html>
<html lang="en">
<head>
<meta charset="utf-8">
<title>Business Card – Terravale Ground Makrz</title>
<link rel="stylesheet" href="https://fonts.googleapis.com/css2?family=Montserrat:wght@400;500;700;800&display=swap">
<style>
  :root {
    --stage: #3a3a3a;
    --card-dark: #0d0d0d;
    --card-dark-tone: #1c1c1c;
    --card-light: #ffffff;
    --ink: #111111;
    --ink-soft: #2a2a2a;
    --accent: #f5b21b;
    --on-dark: #f2f2f2;
    --on-dark-soft: #9a9a9a;
  }
  * { box-sizing: border-box; margin: 0; padding: 0; }
  html, body {
    width: 1200px; height: 1186px; overflow: hidden;
    background: var(--stage);
    font-family: "Montserrat", Arial, sans-serif;
  }
  .canvas {
    position: relative; width: 1200px; height: 1186px;
    display: flex; flex-direction: column; align-items: center; justify-content: center; gap: 60px;
  }
  .card {
    position: relative; width: 700px; height: 400px; border-radius: 26px; overflow: hidden;
    box-shadow: 0 14px 30px rgba(0,0,0,.45);
  }
  /* Back */
  .card--back { background: var(--card-dark); }
  .back-pattern {
    position: absolute; inset: 0;
    background: radial-gradient(circle at 40% 45%, var(--card-dark-tone), var(--card-dark) 75%);
  }
  .back-content {
    position: absolute; right: 70px; top: 140px; width: 300px;
    display: flex; flex-direction: column; gap: 12px;
  }
  .back-mark {
    display: flex; align-items: center; gap: 10px;
    color: var(--on-dark); font-weight: 700; font-size: 15px; letter-spacing: 1px; white-space: nowrap;
  }
  .back-mark .dot { width: 14px; height: 14px; border-radius: 50%; background: var(--on-dark); flex: none; }
  .back-services {
    color: var(--on-dark-soft); font-weight: 500; font-size: 12px; line-height: 1.5; letter-spacing: .6px;
    padding-left: 24px;
  }
  /* Front */
  .card--front { background: var(--card-light); color: var(--ink); }
  .brand {
    position: absolute; left: 48px; top: 44px;
    display: flex; flex-direction: column; gap: 8px;
  }
  .brand-row { display: flex; align-items: center; gap: 12px; }
  .brand .dot { flex: none; width: 44px; height: 44px; border-radius: 50%; background: var(--ink); }
  .brand-name { font-weight: 800; font-size: 19px; line-height: 1.15; letter-spacing: .5px; color: var(--ink); white-space: nowrap; }
  .brand-phone { padding-left: 56px; font-weight: 800; font-size: 12px; letter-spacing: 5px; color: var(--ink); white-space: nowrap; }
  .person { position: absolute; left: 48px; top: 190px; }
  .person-name { color: var(--accent); font-weight: 800; font-size: 28px; letter-spacing: .5px; }
  .person-role { font-size: 16px; color: var(--ink-soft); margin-top: 4px; }
  .contacts { list-style: none; margin-top: 14px; display: flex; flex-direction: column; gap: 9px; }
  .contacts li { display: flex; align-items: center; gap: 12px; font-size: 16px; color: var(--ink-soft); letter-spacing: .3px; white-space: nowrap; }
  .contacts svg { width: 16px; height: 16px; flex: none; }
  .hero-mark {
    position: absolute; right: 50px; top: 70px; width: 250px; height: 250px;
    display: flex; align-items: center; justify-content: center; text-align: center;
    font-weight: 800; font-size: 30px; line-height: 1.1; color: var(--ink);
  }
</style>
</head>
<body>
<main class="canvas">
  <section class="card card--back" aria-label="Card back">
    <div class="back-pattern" role="img" aria-label="Repeating tone-on-tone company emblem pattern"></div>
    <div class="back-content">
      <div class="back-mark"><span class="dot"></span>TERRAVALE GROUND MAKRZ</div>
      <p class="back-services">SPECIALIZES IN LAND CLEARING,<br>FORESTRY MULCHING AND EXCAVATION</p>
    </div>
  </section>

  <section class="card card--front" aria-label="Card front">
    <div class="brand">
      <div class="brand-row">
        <span class="dot"></span>
        <span class="brand-name">TERRAVALE GROUND<br>MAKRZ LLC</span>
      </div>
      <div class="brand-phone">555·714·9082</div>
    </div>

    <div class="person">
      <h1 class="person-name">DALE VORSKIN</h1>
      <p class="person-role">Managing Director</p>
      <ul class="contacts">
        <li>
          <svg viewBox="0 0 16 16"><circle cx="8" cy="8" r="8" fill="var(--accent)"/><path d="M5 4.5l1.6-.3.8 2-1 .8a5 5 0 0 0 2.6 2.6l.8-1 2 .8-.3 1.6C9 11.5 4.5 7 5 4.5z" fill="#fff"/></svg>
          555- 714-9082
        </li>
        <li>
          <svg viewBox="0 0 16 16"><rect x="1" y="3" width="14" height="10" rx="1.5" fill="var(--accent)"/><path d="M2 4l6 5 6-5" stroke="#fff" stroke-width="1.3" fill="none"/></svg>
          OFFICE@TRV-GROUNDMAKRZ.COM
        </li>
        <li>
          <svg viewBox="0 0 16 16"><circle cx="8" cy="8" r="7.5" fill="var(--accent)"/><path d="M1 8h14M8 1c-3 3-3 11 0 14M8 1c3 3 3 11 0 14" stroke="#fff" stroke-width="1" fill="none"/></svg>
          WWW.TRV-GROUNDMAKRZ.COM
        </li>
      </ul>
    </div>

    <div class="hero-mark">TERRAVALE<br>GROUND<br>MAKRZ</div>
  </section>
</main>
</body>
</html>
```